business card deign

Logo needs the following on it.
1. attached logo
2. Tagline - "If it chills the cooler or lifts the crowd...we bring it!"
3. Name- Dalton Pikes, Founder and Director
4. Address - 412 E. Carver Avenue, Ste 2207, Brackenport, FL. 33917
5. Phone - 555.318.4726

```html
<!DOCTYPE html>
<html lang="en">
<head>
<meta charset="utf-8">
<title>Hopvale Business Card</title>
<link href="https://fonts.googleapis.com/css2?family=Montserrat:wght@400;500;700&display=swap" rel="stylesheet">
<style>
  :root {
    --backdrop: #e7e7e9;
    --card: #222222;
    --ink-light: #ffffff;
    --ink-soft: #e4e4e4;
    --ink-muted: #c9c9c9;
    --ink-deep: #111111;
    --artwork-hi: rgba(110,110,110,0.45);
    --artwork-lo: rgba(34,34,34,0);
  }
  * { margin: 0; padding: 0; box-sizing: border-box; }
  html, body {
    width: 1200px;
    height: 1108px;
    overflow: hidden;
    background: var(--backdrop);
    font-family: "Montserrat", sans-serif;
  }
  .card {
    position: absolute;
    width: 740px;
    height: 443px;
    background: var(--card);
    overflow: hidden;
  }
  .card--front { left: 241px; top: 68px; }
  .card--back { left: 248px; top: 589px; width: 739px; }

  .brand-name {
    position: absolute;
    font-family: "Montserrat", sans-serif;
    font-weight: 700;
    font-size: 40px;
    letter-spacing: 0.28em;
    line-height: 1;
    white-space: nowrap;
  }
  .card--front .brand-name { left: 37px; top: 67px; color: var(--ink-light); }
  .card--back .brand-name {
    left: 0; right: 0; top: 278px;
    text-align: center;
    padding-left: 0.28em;
    color: var(--ink-deep);
  }

  .holder { position: absolute; right: 47px; top: 56px; text-align: right; }
  .holder__name { font-weight: 700; font-size: 27px; color: var(--ink-light); line-height: 1.1; }
  .holder__title { font-weight: 400; font-size: 16.5px; color: var(--ink-soft); margin-top: 2px; }
  .edge-tab {
    position: absolute; right: 0; top: 60px;
    width: 21px; height: 48px; background: var(--ink-light);
  }

  .address {
    position: absolute; left: 35px; top: 243px;
    font-size: 16px; line-height: 20px; color: var(--ink-soft);
  }
  .contacts { position: absolute; left: 35px; top: 324px; list-style: none; }
  .contacts li {
    display: flex; align-items: center; gap: 10px;
    font-size: 16px; color: var(--ink-soft);
    height: 20px; margin-bottom: 12px;
  }
  .contacts svg { width: 16px; height: 16px; flex: none; }

  .artwork-area { position: absolute; }
  .card--front .artwork-area {
    left: 325px; top: 150px; width: 375px; height: 282px;
    background: radial-gradient(ellipse 60% 70% at 78% 30%, var(--artwork-hi), var(--artwork-lo) 100%);
  }
  .card--back .artwork-area {
    left: 208px; top: 60px; width: 266px; height: 202px;
    background: radial-gradient(ellipse 60% 70% at 78% 30%, var(--artwork-hi), var(--artwork-lo) 100%);
  }

  .tagline {
    position: absolute; left: 0; right: 0; top: 387px;
    text-align: center; font-size: 16px; color: var(--ink-muted);
  }
</style>
</head>
<body>
  <section class="card card--front">
    <div class="brand-name">HOPVALE</div>

    <div class="holder">
      <div class="holder__name">Dalton Pikes</div>
      <div class="holder__title">Founder and Director</div>
    </div>
    <div class="edge-tab"></div>

    <div class="artwork-area" role="img" aria-label="Large decorative brand artwork in soft grey gradient"></div>

    <p class="address">412 E. Carver Avenue, Ste 2207,<br>Brackenport, FL. 33917</p>

    <ul class="contacts">
      <li>
        <svg viewBox="0 0 16 16" aria-hidden="true"><path fill="#fff" d="M3.5 1.5l2.5 3-1.4 1.6c.8 1.8 2.2 3.3 4 4.2l1.6-1.4 3 2.4-1.3 2.4C7 13.4 2.6 9 1.6 3z"/></svg>
        555.318.4726
      </li>
      <li>
        <svg viewBox="0 0 16 16" aria-hidden="true"><rect x="2" y="4" width="12" height="9" rx="1" fill="#fff"/><path d="M2.5 4.5L8 9l5.5-4.5" fill="none" stroke="#222" stroke-width="1.2"/></svg>
        info@hopvale.com
      </li>
      <li>
        <svg viewBox="0 0 16 16" aria-hidden="true"><circle cx="8" cy="8" r="6.5" fill="#fff"/><path d="M1.5 8h13M8 1.5c-2.5 3-2.5 10 0 13M8 1.5c2.5 3 2.5 10 0 13" fill="none" stroke="#222" stroke-width="1"/></svg>
        www.hopvale.com
      </li>
    </ul>
  </section>

  <section class="card card--back">
    <div class="artwork-area" role="img" aria-label="Decorative brand artwork in soft grey gradient"></div>
    <div class="brand-name">HOPVALE</div>
    <p class="tagline">If it chills the cooler or lifts the crowd...we bring it</p>
  </section>
</body>
</html>
```